Upscale business cards needed for Board of Directors

We need professional business cards created for members of our family business Board of Directors. We would like these relatively simple and straightforward, but also with a unique element to set them apart. Probably stick with neutral and simple colors - white, grey etc. We need space for the traditional elements, including name, title, address, email/phone number. And we will be creating several from this template so it needs to be template that is easy to switch information in and out of.
Business
See description

```html
<!DOCTYPE html>
<html lang="en">
<head>
<meta charset="utf-8">
<title>Northmere Holdings – Business Card</title>
<link rel="stylesheet" href="https://fonts.googleapis.com/css2?family=Arimo:wght@400;700&display=swap">
<style>
  :root {
    --stage: #e9e8e6;
    --card-white: #ffffff;
    --card-black: #1c1b1b;
    --card-black-soft: #2c2a2a;
    --gold: #b3a07c;
    --ink: #1a1a1a;
    --ink-grey: #5a5a5a;
    --ink-light: #f4f4f4;
  }
  * { margin: 0; padding: 0; box-sizing: border-box; }
  html, body { width: 1200px; height: 843px; overflow: hidden; }
  body {
    background: var(--stage);
    font-family: "Arimo", Arial, sans-serif;
    position: relative;
  }
  .card {
    position: absolute;
    width: 620px;
    height: 354px;
    border-radius: 3px;
    overflow: hidden;
    box-shadow: 0 6px 18px rgba(0,0,0,0.18);
  }
  /* Back of card */
  .card--back {
    left: 90px;
    top: 60px;
    background: linear-gradient(160deg, var(--card-black-soft), var(--card-black) 60%);
    display: flex;
    flex-direction: column;
    align-items: center;
    justify-content: center;
  }
  .card--back .wordmark { color: var(--ink-light); font-size: 40px; }
  .card--back .wordmark__sub { color: var(--ink-light); font-size: 24px; }
  .card--back .back-web {
    margin-top: 22px;
    color: var(--ink-light);
    font-size: 13px;
    letter-spacing: 2px;
  }
  /* Wordmark */
  .wordmark {
    font-weight: 700;
    text-transform: uppercase;
    letter-spacing: 1px;
    line-height: 1;
    text-align: center;
    white-space: nowrap;
  }
  .wordmark__sub { display: block; letter-spacing: 9px; margin-top: 6px; }
  /* Front of card */
  .card--front {
    left: 490px;
    top: 450px;
    background: var(--card-white);
  }
  .card--front .wordmark {
    position: absolute;
    left: 60px;
    top: 40px;
    color: var(--ink);
    font-size: 34px;
  }
  .card--front .wordmark__sub { font-size: 20px; }
  .person { position: absolute; left: 60px; top: 150px; }
  .person__name { color: var(--ink); font-size: 19px; letter-spacing: 0.5px; white-space: nowrap; }
  .person__title { color: var(--gold); font-size: 14px; letter-spacing: 0.5px; margin-top: 4px; }
  .contact {
    position: absolute;
    right: 30px;
    top: 200px;
    width: 250px;
    color: var(--ink-grey);
    font-size: 13.5px;
    line-height: 1.3;
    white-space: nowrap;
  }
  .contact__address { margin-bottom: 10px; }
  .contact__row { display: flex; gap: 6px; align-items: baseline; }
  .contact__label {
    color: var(--ink);
    font-weight: 700;
    flex: 0 0 26px;
    white-space: nowrap;
  }
  .card__band {
    position: absolute;
    left: 0; right: 0; bottom: 0;
    height: 18px;
    display: flex;
  }
  .card__band-dark { width: 45%; background: linear-gradient(90deg, var(--card-black), var(--card-black-soft)); }
  .card__band-gold { flex: 1; background: var(--gold); }
</style>
</head>
<body>
  <section class="card card--back" aria-label="Card back">
    <div class="wordmark">Northmere<span class="wordmark__sub">Holdings</span></div>
    <div class="back-web">www.northmere.com</div>
  </section>

  <section class="card card--front" aria-label="Card front">
    <div class="wordmark">Northmere<span class="wordmark__sub">Holdings</span></div>
    <div class="person">
      <div class="person__name">DANIEL REYES</div>
      <div class="person__title">PRESIDENT</div>
    </div>
    <div class="contact">
      <div class="contact__address">2716 Linden Court<br>Maple Grove, NY 11020</div>
      <div class="contact__row"><span class="contact__label">P :</span><span>555 0142 7788</span></div>
      <div class="contact__row"><span class="contact__label">E :</span><span>daniel@northmere.com</span></div>
      <div class="contact__row"><span class="contact__label">W :</span><span>www.northmere.com</span></div>
    </div>
    <div class="card__band">
      <div class="card__band-dark"></div>
      <div class="card__band-gold"></div>
    </div>
  </section>
</body>
</html>
```